Construction business card

I need a new business card, they can connect with my logo, brand.
What we do is residential house , design and build
I like: Navy blue / black
I attached our logo, brand,
and, some idea for business card.

```html
<!DOCTYPE html>
<html lang="en">
<head>
<meta charset="utf-8">
<title>Ridgeline Building Group – Business Card</title>
<link href="https://fonts.googleapis.com/css2?family=Arimo:wght@400;700&family=Kanit:wght@400&display=swap" rel="stylesheet">
<style>
  :root {
    --bg-top: #adc8cb;
    --bg-bottom: #dcfafa;
    --card-navy: #020a24;
    --brand-blue: #3d87d6;
    --text-white: #ffffff;
    --text-soft: #e6ecf5;
  }
  * { margin: 0; padding: 0; box-sizing: border-box; }
  html, body { width: 1200px; height: 1200px; overflow: hidden; }
  body {
    background: linear-gradient(180deg, var(--bg-top), var(--bg-bottom));
    font-family: "Arimo", Arial, sans-serif;
    position: relative;
  }
  .card {
    position: absolute;
    left: 180px;
    width: 840px;
    height: 480px;
    background: var(--card-navy);
    box-shadow: 0 18px 40px rgba(20, 50, 60, 0.25);
    overflow: hidden;
  }
  .card--front { top: 90px; }
  .card--back { top: 630px; }

  .wordmark {
    position: absolute;
    display: flex;
    align-items: center;
    gap: 14px;
    color: var(--text-white);
    font-family: "Arimo", Arial, sans-serif;
    font-weight: 700;
    font-size: 34px;
    line-height: 1.1;
    letter-spacing: 0.5px;
  }
  .wordmark__square {
    width: 22px; height: 22px;
    background: var(--brand-blue);
    flex: none;
  }
  .card--front .wordmark { left: 50%; top: 120px; transform: translateX(-50%); white-space: nowrap; }
  .card--back .wordmark { left: 70px; top: 110px; }

  .person {
    position: absolute;
    right: 470px;
    top: 305px;
    text-align: right;
  }
  .person__name {
    font-family: "Kanit", Arial, sans-serif;
    font-weight: 400;
    font-size: 40px;
    color: var(--brand-blue);
    line-height: 1;
    letter-spacing: 1px;
  }
  .person__role {
    font-size: 16px;
    color: var(--text-white);
    margin-top: 6px;
  }
  .divider {
    position: absolute;
    left: 420px;
    top: 290px;
    width: 4px;
    height: 150px;
    background: var(--brand-blue);
  }
  .contact {
    position: absolute;
    left: 470px;
    top: 300px;
    list-style: none;
    color: var(--text-soft);
    font-size: 18px;
    line-height: 1.3;
  }
  .contact__item {
    display: flex;
    align-items: flex-start;
    gap: 16px;
    margin-bottom: 10px;
  }
  .contact__item--address { margin-bottom: 16px; }
  .contact__icon { width: 20px; height: 20px; flex: none; margin-top: 1px; }
</style>
</head>
<body>

  <section class="card card--front" aria-label="Business card front">
    <div class="wordmark"><span class="wordmark__square"></span>Ridgeline Building Group</div>

    <div class="person">
      <p class="person__name">Alex Morgan</p>
      <p class="person__role">Manager</p>
    </div>

    <div class="divider"></div>

    <ul class="contact">
      <li class="contact__item contact__item--address">
        <svg class="contact__icon" viewBox="0 0 20 20" aria-hidden="true"><path d="M10 1a7 7 0 0 0-7 7c0 5 7 11 7 11s7-6 7-11a7 7 0 0 0-7-7z" fill="var(--brand-blue)"/><circle cx="10" cy="8" r="2.6" fill="var(--card-navy)"/></svg>
        <span>48 Harbour Lane,<br>Eastfield, Vic 3190</span>
      </li>
      <li class="contact__item">
        <svg class="contact__icon" viewBox="0 0 20 20" aria-hidden="true"><path d="M5 2l3 4-2 2a11 11 0 0 0 6 6l2-2 4 3-2 3C9 18 2 11 2 4z" fill="var(--brand-blue)"/></svg>
        <span>0400 555 018</span>
      </li>
      <li class="contact__item">
        <svg class="contact__icon" viewBox="0 0 20 20" aria-hidden="true"><rect x="1.5" y="4" width="17" height="12" fill="none" stroke="var(--brand-blue)" stroke-width="2"/><path d="M2 5l8 6 8-6" fill="none" stroke="var(--brand-blue)" stroke-width="2"/></svg>
        <span>hello@ridgelinebuild.com.au</span>
      </li>
      <li class="contact__item">
        <svg class="contact__icon" viewBox="0 0 20 20" aria-hidden="true"><g fill="none" stroke="var(--brand-blue)" stroke-width="1.6"><circle cx="10" cy="10" r="8"/><ellipse cx="10" cy="10" rx="3.5" ry="8"/><path d="M2 10h16M3.5 6h13M3.5 14h13"/></g></svg>
        <span>www.ridgelinebuild.com.au</span>
      </li>
    </ul>
  </section>

  <section class="card card--back" aria-label="Business card back">
    <div class="wordmark"><span class="wordmark__square"></span>Ridgeline Building Group</div>
  </section>

</body>
</html>
```